National Intensive Course Provider needs an advert designed to appear in trams

We need an advertisement designed to put in trams, the dimensions are 660mm wide and 203mm height. We offer intensive driving courses all over the UK, allowing pupils to complete a full driving course within a week/two weeks with both the theory and practical tests included in the course (as required). We would like the colours used to be green and dark blue, maybe red also, whatever looks best from them colours really.

Key Points to highlight:
- Pass your driving test within 1 week
- Start your course as early as next week
- Both tests included as part of your course (if required)

I have attached some images which could be included in the design

```html
<!DOCTYPE html>
<html lang="en">
<head>
<meta charset="utf-8">
<title>Swiftlane Driving Courses – Tram Advert</title>
<link rel="stylesheet" href="https://fonts.googleapis.com/css2?family=Roboto+Condensed:wght@700;800&family=Open+Sans:wght@700&display=swap">
<style>
  :root {
    --page: #ffffff;
    --red: #fe0000;
    --red-deep: #d80000;
    --green: #8dc53f;
    --purple: #4f3585;
    --navy: #111a4a;
    --white: #ffffff;
    --shadow: rgba(0, 0, 0, 0.45);
  }
  * { margin: 0; padding: 0; box-sizing: border-box; }
  html, body {
    width: 1200px;
    height: 391px;
    overflow: hidden;
    background: var(--page);
  }
  .advert {
    position: relative;
    width: 1200px;
    height: 391px;
    background: var(--page);
  }
  .advert__backdrop {
    position: absolute;
    left: 0;
    top: 0;
  }
  .headline {
    position: absolute;
    left: 60px;
    top: 52px;
    font-family: "Roboto Condensed", "Arial Narrow", sans-serif;
    font-weight: 800;
    color: var(--white);
    text-shadow: 2px 2px 3px var(--shadow);
    line-height: 1;
  }
  .headline__lead {
    display: block;
    font-size: 55px;
    letter-spacing: 0.5px;
  }
  .headline__sub {
    display: block;
    margin-top: 6px;
    font-size: 55px;
    letter-spacing: 0.5px;
  }
  .brand {
    position: absolute;
    left: 60px;
    top: 214px;
    width: 204px;
    height: 138px;
    border-radius: 22px;
    background: var(--navy);
    display: flex;
    align-items: center;
    justify-content: center;
    text-align: center;
  }
  .brand__name {
    font-family: "Roboto Condensed", "Arial Narrow", sans-serif;
    font-weight: 700;
    font-size: 26px;
    line-height: 1.15;
    color: var(--white);
    text-transform: uppercase;
    letter-spacing: 1px;
  }
  .pupil-photo {
    position: absolute;
    left: 282px;
    top: 213px;
    width: 172px;
    height: 139px;
    border-radius: 14px;
    background: linear-gradient(160deg, #6f8a4a 0%, #4d6b3a 45%, #c0202a 100%);
  }
  .included-note {
    position: absolute;
    left: 468px;
    top: 228px;
    font-family: "Open Sans", Arial, sans-serif;
    font-weight: 700;
    font-size: 24px;
    line-height: 35px;
    color: var(--white);
  }
  .promise {
    position: absolute;
    right: 60px;
    top: 50px;
    font-family: "Roboto Condensed", "Arial Narrow", sans-serif;
    font-weight: 700;
    font-size: 74px;
    line-height: 76px;
    color: var(--white);
    text-align: right;
    text-shadow: 2px 2px 3px var(--shadow);
  }
</style>
</head>
<body>
  <main class="advert">
    <svg class="advert__backdrop" width="1200" height="391" viewBox="0 0 1200 391" aria-hidden="true">
      <rect class="band-red" x="20" y="24" width="1164" height="346" fill="var(--red)"/>
      <polygon class="accent-shadow" points="718,70 748,64 822,370 796,370" fill="var(--red-deep)"/>
      <polygon class="accent-purple" points="724,72 752,66 824,370 812,370" fill="var(--purple)"/>
      <polygon class="panel-green" points="744,24 1184,24 1184,370 824,370" fill="var(--green)"/>
    </svg>

    <h1 class="headline">
      <span class="headline__lead">START YOUR COURSE</span>
      <span class="headline__sub">as early as Next Week</span>
    </h1>

    <div class="brand">
      <span class="brand__name">Swiftlane<br>Driving Courses</span>
    </div>

    <div class="pupil-photo" role="img" aria-label="Photo of a smiling pupil holding a driving test pass certificate beside a red learner car"></div>

    <p class="included-note">Theory and practical<br>tests included as part of<br>your course (if required)</p>

    <h2 class="promise">Pass Your<br>Driving Test<br>Within<br>1 Week</h2>
  </main>
</body>
</html>
```